Product Label with Company Logo & Product Information

I am looking for a new label design for one of my products, Candied Pecans. I am including an old label that I made, but it does not "pop" on the current packaging. See image of current packaging attached as well.

I want the design to ultimately be something that I can take and order a roll of labels/stickers. Please stick within standard label/sticker sizes (round or square). Please include final size as well.

Must Haves:
(1) Company logo (any color variation-see attached logo images).
(2) All wording on the old label
(3) Label size can not be more than 2 in. x 4 in. (I would actually like them a little smaller). They seem kind of big as they are right now.

```html
<!DOCTYPE html>
<html lang="en">
<head>
<meta charset="utf-8">
<title>Gourmet Candied Pecans Label</title>
<link href="https://fonts.googleapis.com/css2?family=Abril+Fatface&family=Rye&family=Roboto:wght@700&display=swap" rel="stylesheet">
<style>
  :root {
    --stage: #232323;
    --card-dark: #1f1f23;
    --card-grey: #58585a;
    --band-grey: #4a4a4d;
    --honey: #f2e82a;
  }
  * { margin: 0; padding: 0; box-sizing: border-box; }
  html, body { width: 1200px; height: 780px; overflow: hidden; background: var(--stage); }
  .canvas { position: relative; width: 1200px; height: 780px; }
  .label {
    position: absolute; left: 100px; top: 90px; width: 1000px; height: 600px;
    border: 6px solid var(--honey); border-radius: 44px; overflow: hidden;
    background: var(--card-dark);
  }
  .label__waves { position: absolute; inset: 0; width: 100%; height: 100%; }
  .headline { position: absolute; left: 56px; top: 70px; }
  .headline__top {
    font-family: "Abril Fatface", serif; font-size: 78px; color: var(--honey);
    letter-spacing: 2px; line-height: 1;
  }
  .headline__product {
    font-family: "Rye", serif; font-size: 58px; color: var(--card-grey);
    -webkit-text-stroke: 2px var(--honey); line-height: 1.1; margin-top: 4px;
  }
  .brand {
    position: absolute; right: 70px; top: 110px; display: flex; align-items: center; gap: 18px;
  }
  .brand__dot { width: 26px; height: 26px; border-radius: 50%; background: var(--honey); }
  .brand__name { font-family: "Rye", serif; font-size: 62px; color: var(--honey); line-height: 1; }
  .details {
    position: absolute; left: 70px; bottom: 60px;
    font-family: "Rye", serif; font-size: 26px; color: var(--honey); line-height: 1.6;
  }
  .contact {
    position: absolute; right: 56px; bottom: 40px; display: flex; align-items: center; gap: 16px;
    font-family: "Roboto", sans-serif; font-weight: 700; font-size: 40px; color: var(--honey);
  }
  .contact__icon { width: 46px; height: 46px; }
</style>
</head>
<body>
<div class="canvas">
  <div class="label">
    <svg class="label__waves" viewBox="0 0 988 588" preserveAspectRatio="none" aria-hidden="true">
      <path d="M0,380 C260,300 560,300 988,330 L988,588 L0,588 Z" fill="var(--band-grey)"/>
      <path d="M0,400 C280,322 600,340 988,420 L988,588 L0,588 Z" fill="var(--card-grey)"/>
      <path d="M60,392 C300,318 620,318 988,350 L988,378 C640,350 320,340 60,392 Z" fill="var(--honey)"/>
    </svg>

    <div class="headline">
      <div class="headline__top">GOURMET</div>
      <div class="headline__product">CANDIED PECANS</div>
    </div>

    <div class="brand">
      <span class="brand__dot"></span>
      <span class="brand__name">Tidy Wren</span>
    </div>

    <div class="details">
      <p>Made with Cinnamon</p>
      <p>Brown Sugar &amp; Salt Order More</p>
      <p>Tidy Wren Market, LLC</p>
    </div>

    <div class="contact">
      <svg class="contact__icon" viewBox="0 0 46 46" aria-hidden="true">
        <polygon points="23,2 42,12.5 42,33.5 23,44 4,33.5 4,12.5" fill="var(--honey)"/>
        <path d="M15,14 l5,-2 l3,6 l-3,2 c1,3 3,5 6,6 l2,-3 l6,3 l-2,5 c-10,0 -17,-7 -17,-17 Z" fill="var(--card-grey)"/>
      </svg>
      <span class="contact__phone">(555)014-2287</span>
    </div>
  </div>
</div>
</body>
</html>
```